Retail swing tag labels for a sale / reduction

We need some graphics done to be made into retail swing tag labels, for the purpose of reductions on selected products.

We have attached 2 examples of previous designs that were similar idea, but more themed for 'autumn' and 'winter'. This theme will just have the word 'REDUCED'.

The white areas can be smaller in size, as we would like to include a large "20% OFF" at the bottom, and then a 30%, 40%, 50% option.

Overall colour scheme should be red background with some form of detailed patterning (see previous examples). Bright and e-catching.

Any other questions, just ask.

The screenshot is front the printers, but in horizontal orientation.

The finished dimensions will be A6 portrait, printed both sides.

We have also included the vector file of the shop "Hollowmere Furnishings", which can be included on 1 of the sides.

```html
<!DOCTYPE html>
<html lang="en">
<head>
<meta charset="utf-8">
<title>Hollowmere Furnishings – Reduced Swing Tags</title>
<link rel="stylesheet" href="https://fonts.googleapis.com/css2?family=Montserrat:wght@300;700;800&display=swap">
<style>
  :root {
    --sheet-top: #c9c9c9;
    --sheet-bottom: #ffffff;
    --frame-light: rgba(255,255,255,0.55);
    --red-bright: #e3263a;
    --red-mid: #c81d33;
    --red-deep: #8e1226;
    --red-glow: #f0503f;
    --panel-white: #ffffff;
    --text-white: #ffffff;
    --text-red: #c81d33;
  }
  * { box-sizing: border-box; margin: 0; padding: 0; }
  html, body { width: 917px; height: 1200px; overflow: hidden; }
  body {
    position: relative;
    background: linear-gradient(180deg, var(--sheet-top) 0%, var(--sheet-bottom) 100%);
    font-family: "Montserrat", Arial, sans-serif;
  }
  .tag {
    position: absolute;
    width: 379px;
    height: 530px;
    overflow: hidden;
    box-shadow: 4px 6px 10px rgba(0,0,0,0.45);
  }
  .tag--20 { left: 61px; top: 50px; }
  .tag--30 { left: 476px; top: 50px; }
  .tag--40 { left: 61px; top: 616px; }
  .tag--50 { left: 476px; top: 616px; }

  .tag__art {
    position: absolute;
    inset: 0;
    background:
      radial-gradient(ellipse 60% 40% at 30% 25%, var(--red-glow) 0%, transparent 70%),
      radial-gradient(ellipse 50% 40% at 80% 60%, var(--red-bright) 0%, transparent 70%),
      linear-gradient(160deg, var(--red-mid) 0%, var(--red-deep) 100%);
  }

  .tag__frame {
    position: absolute;
    inset: 10px;
    border: 1px solid var(--frame-light);
  }

  .tag__headline {
    position: absolute;
    top: 96px;
    left: 0; right: 0;
    text-align: center;
    font-weight: 800;
    font-size: 46px;
    letter-spacing: 0;
    color: var(--text-white);
  }

  .brand {
    position: absolute;
    top: 236px;
    left: 0; right: 0;
    display: flex;
    flex-direction: column;
    align-items: center;
    gap: 10px;
  }
  .brand__mark { width: 14px; height: 14px; background: var(--text-white); }
  .brand__name {
    font-weight: 300;
    font-size: 11px;
    letter-spacing: 2px;
    text-transform: uppercase;
    color: var(--text-white);
  }

  .offer {
    position: absolute;
    left: 24px; right: 24px;
    bottom: 28px;
    height: 140px;
    background: var(--panel-white);
    display: flex;
    align-items: center;
    justify-content: center;
  }
  .offer__value {
    font-weight: 800;
    font-size: 62px;
    line-height: 1;
    color: var(--text-red);
    white-space: nowrap;
  }
</style>
</head>
<body>
  <article class="tag tag--20">
    <div class="tag__art" role="img" aria-label="Bright red background with detailed decorative red patterning"></div>
    <div class="tag__frame"></div>
    <h1 class="tag__headline">REDUCED</h1>
    <div class="brand"><span class="brand__mark"></span><span class="brand__name">Hollowmere Furnishings</span></div>
    <div class="offer"><span class="offer__value">20% OFF</span></div>
  </article>

  <article class="tag tag--30">
    <div class="tag__art" role="img" aria-label="Bright red background with detailed decorative red patterning"></div>
    <div class="tag__frame"></div>
    <h2 class="tag__headline">REDUCED</h2>
    <div class="brand"><span class="brand__mark"></span><span class="brand__name">Hollowmere Furnishings</span></div>
    <div class="offer"><span class="offer__value">30% OFF</span></div>
  </article>

  <article class="tag tag--40">
    <div class="tag__art" role="img" aria-label="Bright red background with detailed decorative red patterning"></div>
    <div class="tag__frame"></div>
    <h2 class="tag__headline">REDUCED</h2>
    <div class="brand"><span class="brand__mark"></span><span class="brand__name">Hollowmere Furnishings</span></div>
    <div class="offer"><span class="offer__value">40% OFF</span></div>
  </article>

  <article class="tag tag--50">
    <div class="tag__art" role="img" aria-label="Bright red background with detailed decorative red patterning"></div>
    <div class="tag__frame"></div>
    <h2 class="tag__headline">REDUCED</h2>
    <div class="brand"><span class="brand__mark"></span><span class="brand__name">Hollowmere Furnishings</span></div>
    <div class="offer"><span class="offer__value">50% OFF</span></div>
  </article>
</body>
</html>
```